Recruitment of Trellan Staffing for the UK market

I want a website for the UK market to attract businesses and companies to come to us for Philipine labour. We want an information site that gives all information on what we do and how we can recruit Philippine labour.
This is a recruitment site for companies to contact us with their requirements for skilled workers coming from the Philipines over to the UK to work.

Target Market(s)

Uk Companies and businesses who want Philipine skilled workers

Industry/Entity Type

REcruitment

Coding

Number of Pages Required

5+ page

Font styles to use
Sans Serif

Colors
0054AA
0677BA
7BADD7
CADEEF
E8F1F8
0094D4
00A9DD
6FCCEA
C7EBF8
E9F6FB
EE7325
F08F49
F5BC92
FAE3D3
FDF4ED
EB3D1F
EC4F4E
F09395
F8D3D4
FCEDEE

Requirements
Must have
• Look professional and corperate with drop down menus for Home ,about, services,articles. training , contact us
Nice to have
• Look at Velmora recruitment- https://velmorarecruitment.example.co.uk/. This is my current site - https://www.trellanstaffing.example.com/
Should not have
• Cartoons or silly pictures , needs to be corperate looking

```html
<!DOCTYPE html>
<html lang="en">
<head>
<meta charset="utf-8">
<title>Trellan Staffing – Skilled Philippine Workers for UK Companies</title>
<link rel="stylesheet" href="https://fonts.googleapis.com/css2?family=Bebas+Neue&family=Mulish:wght@400;500;600;700&family=Poppins:wght@400;500;600&display=swap">
<style>
:root{
  --blue:#0054AA;
  --blue-mid:#0677BA;
  --sky:#0094D4;
  --pale:#E8F1F8;
  --pale-card:#E9F6FB;
  --orange:#EE7325;
  --orange-pale:#FDF4ED;
  --red:#EB3D1F;
  --logo-red:#8b1e22;
  --ink:#1d1d1f;
  --text:#555a60;
  --navy:#0b1740;
  --line:#e6e9ee;
  --white:#ffffff;
}
*{box-sizing:border-box;margin:0;padding:0}
html,body{width:1200px;height:3562px;overflow:hidden}
body{position:relative;background:var(--white);font-family:"Poppins",sans-serif;color:var(--ink)}
.abs{position:absolute}
a{color:inherit;text-decoration:none}

/* header */
.site-header{position:absolute;left:0;top:0;width:1200px;height:65px;background:var(--white)}
.brand{position:absolute;left:162px;top:16px;font-family:"Poppins",sans-serif;font-weight:600;font-size:24px;color:var(--logo-red);letter-spacing:.2px}
.main-nav{position:absolute;top:17px;left:0;width:1200px;font-size:14px;color:#222}
.main-nav a{position:absolute;white-space:nowrap}
.main-nav a.active{color:var(--blue-mid)}

/* hero */
.hero{position:absolute;left:0;top:65px;width:1200px;height:449px;background:linear-gradient(90deg,#3c4a5c 0%,#5d6b78 40%,#3a434f 75%,#262c35 100%)}
.hero-title{position:absolute;left:163px;top:200px;font-family:"Bebas Neue",sans-serif;font-size:45px;line-height:47px;color:var(--white);letter-spacing:.3px}
.hero-title .accent{color:var(--orange);border-bottom:4px solid var(--red)}
.contact-card{position:absolute;left:740px;top:141px;width:298px;height:408px;background:var(--white);box-shadow:0 4px 18px rgba(0,0,0,.14);border:7px solid #d9dde2;border-top-color:#cfd4da}
.contact-card h2{position:absolute;left:0;top:0;width:284px;height:57px;background:var(--blue);color:var(--white);font-family:"Mulish",sans-serif;font-weight:700;font-size:28px;line-height:57px;text-align:center}
.field{position:absolute;left:11px;width:262px;background:var(--orange-pale);font-family:"Poppins",sans-serif;font-size:14px;color:#222;padding:10px 19px;border:1px solid #f4e9de}
.submit{position:absolute;left:11px;top:326px;width:262px;height:41px;background:var(--orange);color:var(--white);font-family:"Poppins",sans-serif;font-weight:600;font-size:18px;letter-spacing:.5px;text-align:center;line-height:41px}

/* about */
.about-photo{position:absolute;left:162px;top:676px;width:359px;height:357px;background:linear-gradient(135deg,#c9cdd6,#e7d9c6 55%,#a7b2bf)}
.about-bar{position:absolute;left:162px;top:1041px;width:191px;height:6px;background:var(--blue-mid)}
.about-inset{position:absolute;left:352px;top:909px;width:203px;height:191px;background:var(--white);padding:6px}
.about-inset div{width:100%;height:100%;background:linear-gradient(135deg,#6a737c,#b8bdbf 50%,#4c5560)}
.eyebrow{font-family:"Mulish",sans-serif;font-weight:700;font-size:14px;letter-spacing:1.5px;color:var(--red)}
.about-title{position:absolute;left:605px;top:718px;font-family:"Mulish",sans-serif;font-weight:600;font-size:38px;color:#222}
.dots{position:absolute;left:608px;top:776px;width:52px;height:3px;background:radial-gradient(circle,var(--sky) 1.2px,transparent 1.6px) 0 0/5px 3px}
.about-lead{position:absolute;left:607px;top:802px;width:430px;font-family:"Mulish",sans-serif;font-size:15px;line-height:26px;color:#333}
.about-body{position:absolute;left:607px;top:862px;width:430px;font-family:"Mulish",sans-serif;font-size:13.5px;line-height:24.5px;color:var(--text)}
.btn-red{position:absolute;left:607px;top:988px;width:132px;height:37px;background:var(--red);color:var(--white);font-family:"Mulish",sans-serif;font-size:14px;display:flex;align-items:center;justify-content:center;gap:7px}

/* working together */
.team-band{position:absolute;left:0;top:1178px;width:1200px;height:539px;background:linear-gradient(90deg,#243559,#2f4266 45%,#2b3c61 70%,#3a4a6e)}
.team-copy{position:absolute;left:0;top:1271px;width:1200px;text-align:center;color:var(--white)}
.team-copy .label{font-family:"Mulish",sans-serif;font-weight:600;font-size:14px;letter-spacing:2px}
.team-copy h2{margin-top:4px;font-family:"Mulish",sans-serif;font-weight:600;font-size:34px;line-height:41px}
.map{position:absolute;left:200px;top:1446px;width:795px;height:527px;background:linear-gradient(160deg,#8eaef2,#87a9f0);box-shadow:0 6px 20px rgba(0,0,0,.18)}

/* services grid */
.grid-line-v{position:absolute;left:596px;top:2035px;width:1px;height:550px;background:var(--line)}
.grid-line-h{position:absolute;left:169px;top:2309px;width:862px;height:1px;background:var(--line)}
.svc{position:absolute;width:360px}
.svc h3{font-family:"Mulish",sans-serif;font-weight:600;font-size:20px;color:#222;margin-top:14px}
.svc p{margin-top:10px;font-family:"Mulish",sans-serif;font-size:13px;line-height:23px;color:var(--text)}
.svc .more{display:flex;align-items:center;gap:5px;margin-top:10px;font-family:"Mulish",sans-serif;font-weight:600;font-size:12.5px;color:var(--red)}

/* cards */
.card{position:absolute;top:2748px;width:270px;height:325px;background:var(--pale-card);text-align:center;font-family:"Poppins",sans-serif}
.card svg{margin-top:42px}
.card h3{margin-top:32px;font-weight:500;font-size:17px;color:#111}
.card p{margin:10px auto 0;width:230px;font-size:14px;line-height:22px;color:#222}
.card .btn{position:absolute;left:78px;top:248px;width:114px;height:36px;background:var(--blue);color:var(--white);font-size:14px;line-height:36px}
.card.featured{background:var(--blue)}
.card.featured h3,.card.featured p{color:var(--white)}
.card.featured .btn{background:var(--white);color:var(--blue)}

/* footer */
.site-footer{position:absolute;left:0;top:3187px;width:1200px;height:375px;background:var(--navy);color:var(--white)}
.footer-brand{position:absolute;left:162px;top:116px;font-weight:600;font-size:22px;color:#e4e7ee}
.social{position:absolute;top:165px;width:28px;height:28px;border-radius:50%;background:var(--blue-mid)}
.footer-head{position:absolute;top:106px;font-family:"Mulish",sans-serif;font-weight:700;font-size:18px}
.footer-links a{position:absolute;font-family:"Mulish",sans-serif;font-size:14px;color:#e6e9f2}
.footer-links a::before{content:"›";margin-right:8px}
.footer-rule{position:absolute;height:1px;background:#223060}
.contact-row{position:absolute;left:748px;display:flex;gap:10px;font-family:"Mulish",sans-serif;font-size:14px;line-height:20px;color:#e6e9f2}
.contact-row svg{flex:none;margin-top:2px}
.copyright{position:absolute;left:0;top:301px;width:1200px;height:74px;border-top:1px solid #1d2a55;text-align:center;line-height:74px;font-family:"Mulish",sans-serif;font-size:14px;color:#e6e9f2}
</style>
</head>
<body>

<header class="site-header">
  <a class="brand" href="#">Trellan Staffing</a>
  <nav class="main-nav">
    <a class="active" style="left:543px" href="#">Home</a>
    <a style="left:618px" href="#">About</a>
    <a style="left:695px" href="#">Services</a>
    <a style="left:787px" href="#">Articles</a>
    <a style="left:874px" href="#">Training</a>
    <a style="left:962px" href="#">Contact Us</a>
  </nav>
</header>

<section class="hero" role="img" aria-label="Two smiling engineers in hard hats and workwear, one holding a laptop"></section>
<h1 class="hero-title">Recruiting and placing<br>skilled <span class="accent">Philippine workers</span><br>into UK companies</h1>

<form class="contact-card">
  <h2>Contact Us Today</h2>
  <div class="field" style="top:59px;height:41px">Name*</div>
  <div class="field" style="top:112px;height:41px">Email*</div>
  <div class="field" style="top:163px;height:41px">Phone*</div>
  <div class="field" style="top:214px;height:93px">Message*</div>
  <div class="submit">SUBMIT NOW</div>
</form>

<section class="about">
  <div class="about-photo" role="img" aria-label="Smiling engineer in a yellow hard hat beside a colleague with a clipboard"></div>
  <div class="about-bar"></div>
  <div class="about-inset"><div role="img" aria-label="Two technicians in helmets inspecting machinery"></div></div>
  <div class="eyebrow abs" style="left:607px;top:700px">ABOUT</div>
  <h2 class="about-title">Trellan Staffing</h2>
  <div class="dots"></div>
  <p class="about-lead">We source skilled workers directly from the Philippines to work in the UK.</p>
  <p class="about-body">With offices , training locations and specialist recruiters we can find the highest quality individuals to add value and resources to any UK buisness. We delivery quality based on vast experience over a number of years.</p>
  <a class="btn-red" href="#">Read More
    <svg width="13" height="11" viewBox="0 0 13 11"><path d="M1 5.5h10M7 1.5l4 4-4 4" fill="none" stroke="#fff" stroke-width="1.5"/></svg></a>
</section>

<section>
  <div class="team-band" role="img" aria-label="Group of smiling healthcare workers in blue scrubs, tinted dark blue"></div>
  <div class="team-copy">
    <div class="label">WORKING TOGETHER</div>
    <h2>We recruit the finest talent available with our<br>dedicated 200 strong team. Our centres are<br>highlighted in red dots on the map.</h2>
  </div>
  <div class="map" role="img" aria-label="Map of the Philippines with red dots marking recruitment centres in Luzon, Manila, Batangas, Cebu and Davao"></div>
</section>

<section class="services">
  <div class="grid-line-v"></div>
  <div class="grid-line-h"></div>

  <div class="svc" style="left:199px;top:2064px">
    <svg width="50" height="50" viewBox="0 0 50 50"><circle cx="25" cy="25" r="23" fill="none" stroke="#EB3D1F" stroke-width="2"/><path d="M18.5 19a6.5 6.5 0 1 1 9 6c-2 1-2.5 2.5-2.5 5" fill="none" stroke="#0054AA" stroke-width="2"/><circle cx="25" cy="36" r="1.6" fill="#0054AA"/></svg>
    <h3>What We Do</h3>
    <p>Our company has been estabilished in the Philippines for over 20 years. We have mainly been recruiting philippine workers for the off shore industry in asia but since brexit and the new rules on skilled workers...</p>
    <a class="more" href="#">Read More <svg width="12" height="10" viewBox="0 0 12 10"><path d="M1 5h9M6 1l4 4-4 4" fill="none" stroke="#EB3D1F" stroke-width="1.4"/></svg></a>
  </div>

  <div class="svc" style="left:641px;top:2064px">
    <svg width="80" height="50" viewBox="0 0 80 50"><path d="M3 6l12-4 8 24-12 4z" fill="none" stroke="#0054AA" stroke-width="2"/><path d="M77 6L65 2 57 26l12 4z" fill="none" stroke="#0054AA" stroke-width="2"/><path d="M20 10l10 0 8-4 10 2 10 4M22 26l14 14c2 2 5 0 3-3M30 34l6 6c2 2 5 0 3-3M36 30l6 6c2 2 5 0 3-3M42 28l4 4c2 2 5-1 3-3L40 18l-8 4c-3 1-5-3-2-4l8-6" fill="none" stroke="#EB3D1F" stroke-width="2" stroke-linejoin="round"/></svg>
    <h3>How We Help</h3>
    <p>We work with companies to find skilled workers that meet the UK requirements for Visas and work permits. We guide you through the whole process and deliver highly trained people that add value to your business.</p>
    <a class="more" href="#">Read More <svg width="12" height="10" viewBox="0 0 12 10"><path d="M1 5h9M6 1l4 4-4 4" fill="none" stroke="#EB3D1F" stroke-width="1.4"/></svg></a>
  </div>

  <div class="svc" style="left:199px;top:2339px">
    <svg width="36" height="52" viewBox="0 0 36 52"><path d="M18 50C10 38 3 28 3 18a15 15 0 0 1 30 0c0 10-7 20-15 32z" fill="none" stroke="#EB3D1F" stroke-width="2"/><circle cx="18" cy="17" r="8" fill="none" stroke="#0054AA" stroke-width="2"/><path d="M18 15v6" stroke="#0054AA" stroke-width="2"/><circle cx="18" cy="12" r="1.3" fill="#0054AA"/></svg>
    <h3>Where to start</h3>
    <p>We need to know what your issues are and how we can understand the personnal you require , over what time frame and the number of employees you need. Once this is estabilished we start...</p>
    <a class="more" href="#">Read More <svg width="12" height="10" viewBox="0 0 12 10"><path d="M1 5h9M6 1l4 4-4 4" fill="none" stroke="#EB3D1F" stroke-width="1.4"/></svg></a>
  </div>

  <div class="svc" style="left:641px;top:2339px">
    <svg width="50" height="50" viewBox="0 0 50 50"><path d="M8 6l8-2 6 11-5 4c3 7 8 12 15 15l4-5 11 6-2 8c-18 2-39-19-37-37z" fill="none" stroke="#EB3D1F" stroke-width="2" stroke-linejoin="round"/><path d="M28 12a10 10 0 0 1 10 10M28 5a17 17 0 0 1 17 17" fill="none" stroke="#0054AA" stroke-width="2"/></svg>
    <h3>Contact Us Today</h3>
    <p>Please contact us today with your requirements , this can be care workers ,chef, welders, pipe fitters, caravan cabinet makers, medical workers. The UK list of required skills is extensive and the Philippines offersenglish...</p>
    <a class="more" href="#">Read More <svg width="12" height="10" viewBox="0 0 12 10"><path d="M1 5h9M6 1l4 4-4 4" fill="none" stroke="#EB3D1F" stroke-width="1.4"/></svg></a>
  </div>
</section>

<section class="cards">
  <div class="card" style="left:162px">
    <svg width="58" height="52" viewBox="0 0 58 52"><rect x="4" y="6" width="30" height="42" rx="2" fill="none" stroke="#0054AA" stroke-width="2"/><rect x="13" y="2" width="12" height="7" fill="none" stroke="#0054AA" stroke-width="2"/><path d="M9 18l2 2 4-4M9 28l2 2 4-4M9 38l2 2 4-4M19 19h10M19 29h10M19 39h6" fill="none" stroke="#0677BA" stroke-width="2"/><circle cx="45" cy="30" r="5" fill="none" stroke="#0054AA" stroke-width="2"/><path d="M35 49c0-7 4-12 10-12s10 5 10 12z" fill="none" stroke="#0054AA" stroke-width="2"/></svg>
    <h3>UK Skilled Workers List</h3>
    <p>The UK government since brexit have developed a new system based on points...</p>
    <a class="btn" href="#">Read More</a>
  </div>
  <div class="card featured" style="left:465px">
    <svg width="58" height="52" viewBox="0 0 58 52"><rect x="12" y="2" width="34" height="46" rx="2" fill="none" stroke="#fff" stroke-width="2"/><path d="M28 12h12M28 18h12M18 30h22M18 36h22M18 42h14" stroke="#fff" stroke-width="2"/><circle cx="19" cy="15" r="5" fill="none" stroke="#fff" stroke-width="2"/></svg>
    <h3>Sponsor Licence</h3>
    <p>If you have areas of your business that meet the entry requirements of skilled labour...</p>
    <a class="btn" href="#">Read More</a>
  </div>
  <div class="card" style="left:769px">
    <svg width="58" height="52" viewBox="0 0 58 52"><circle cx="20" cy="8" r="5" fill="none" stroke="#0054AA" stroke-width="2"/><path d="M12 48V24c0-6 4-9 8-9s8 3 8 9v24M2 48h54" fill="none" stroke="#0054AA" stroke-width="2"/><circle cx="42" cy="34" r="11" fill="none" stroke="#0677BA" stroke-width="2"/><path d="M42 27v7l5 3" fill="none" stroke="#0677BA" stroke-width="2"/></svg>
    <h3>Recruitment Timeline</h3>
    <p>Brief us on the job profiles-this is passed on to our teams in the Philippines.</p>
    <a class="btn" href="#">Read More</a>
  </div>
</section>

<footer class="site-footer">
  <div class="footer-brand">Trellan Staffing</div>
  <span class="social" style="left:163px"></span>
  <span class="social" style="left:202px"></span>
  <span class="social" style="left:240px"></span>
  <span class="social" style="left:278px"></span>

  <div class="footer-head" style="left:441px">Quick Links</div>
  <nav class="footer-links">
    <a style="left:441px;top:137px" href="#">Home</a>
    <a style="left:576px;top:137px" href="#">Articles</a>
    <a style="left:441px;top:174px" href="#">About</a>
    <a style="left:576px;top:174px" href="#">Training</a>
    <a style="left:441px;top:211px" href="#">Services</a>
    <a style="left:576px;top:211px" href="#">Contact Us</a>
  </nav>
  <div class="footer-rule" style="left:441px;top:163px;width:224px"></div>
  <div class="footer-rule" style="left:441px;top:200px;width:224px"></div>

  <div class="footer-head" style="left:748px">Contact Details</div>
  <div class="contact-row" style="top:137px">
    <svg width="16" height="20" viewBox="0 0 16 20"><path d="M8 19C4 13 1.5 10 1.5 7a6.5 6.5 0 0 1 13 0c0 3-2.5 6-6.5 12z" fill="#fff"/><circle cx="8" cy="7" r="2.4" fill="#0b1740"/></svg>
    <span>Larkspur Court, Elmridge Elmridge<br>EL4 7 United Kingdom</span>
  </div>
  <div class="footer-rule" style="left:770px;top:182px;width:268px"></div>
  <div class="contact-row" style="top:187px">
    <svg width="18" height="18" viewBox="0 0 18 18"><path d="M3 2l3-1 2 4-2 2c1 2.5 3 4.5 5.5 5.5l2-2 4 2-1 3C10 16 2 8 3 2z" fill="none" stroke="#fff" stroke-width="1.4"/></svg>
    <span>07700900412</span>
  </div>
  <div class="footer-rule" style="left:770px;top:211px;width:268px"></div>
  <div class="contact-row" style="top:214px">
    <svg width="18" height="14" viewBox="0 0 18 14"><rect x="1" y="1" width="16" height="12" fill="none" stroke="#fff" stroke-width="1.4"/><path d="M1 1l8 7 8-7M1 13l6-6M17 13l-6-6" fill="none" stroke="#fff" stroke-width="1.4"/></svg>
    <span>sales@trellanstaffing.example.com</span>
  </div>

  <div class="copyright">© 2023 Trellan Staffing Ltd. All Rights Reserved</div>
</footer>

</body>
</html>
```